Professional Single Page Website Design for Tollbrook Advisory

Tollbrook Advisory is a new business consultancy specializing in providing expert services to small businesses, primarily in the brick-and-mortar retail and food service sectors. We offer a range of services including franchise development and launch, due diligence, and construction management.

Currently, we have a basic website set up at www.tollbrookadvisory.example, but we need a professional touch to enhance its design and functionality.

Project Requirements:
- Single Page Design: For now, we need a single page design that effectively showcases who we are, our services, and contact information.
- Future Expansion: The design should be flexible and scalable for future expansion to include additional pages like specific service offerings, about us, and a dedicated contact page.
- Design Aesthetic: We are looking for a modern yet professional design that aligns with our brand identity.
- Logo: We have a logo that we like, which was also sourced from Pixel Bazaar. The logo files are attached to this project brief.

Key Sections to Include:
- Hero Section: An engaging introduction to Tollbrook Advisory with a strong visual impact.
- About Us: A brief overview of who we are and our mission.
- Team: Section for the profiles of the two principals.
- Services: A clear and concise presentation of our services, including franchise development, due diligence, and construction management.
- Contact Information: Easy-to-find contact details, including a form for inquiries.
- Call to Action: Encouraging visitors to get in touch with us for consultations or further information.

Design Considerations:
- Ensure the design is responsive and mobile-friendly.
- Include high-quality images and icons that complement our services and industry.
- We do not need development services, this is only a design project.

```html
<!DOCTYPE html>
<html lang="en">
<head>
<meta charset="utf-8">
<title>Tollbrook Advisory</title>
<link href="https://fonts.googleapis.com/css2?family=Poppins:wght@400;500;600&display=swap" rel="stylesheet">
<style>
:root{
  --green:#9cc9b2;
  --green-deep:#86bba0;
  --ink:#222a31;
  --text:#2c2c2c;
  --muted:#555;
  --soft:#f4f4f4;
  --white:#fff;
}
*{box-sizing:border-box;margin:0;padding:0}
html,body{width:1200px;height:3534px;overflow:hidden}
body{font-family:"Poppins",sans-serif;color:var(--text);background:var(--white);position:relative}
.accent{color:var(--green)}
.btn{display:inline-block;background:var(--green);color:var(--ink);font-size:13px;padding:11px 26px;border-radius:2px;font-family:"Poppins",sans-serif}
.abs{position:absolute}

/* hero */
.hero{position:absolute;left:0;top:0;width:1200px;height:700px;overflow:hidden}
.hero-photo{position:absolute;inset:0;background:linear-gradient(100deg,#3a3631 0%,#5b564e 40%,#8c8a84 70%,#cfcdc6 100%)}
.hero-shade{position:absolute;inset:0;background:linear-gradient(90deg,rgba(20,20,20,.55),rgba(20,20,20,.1) 70%)}
.nav{position:absolute;top:22px;left:141px;right:141px;display:flex;align-items:center;justify-content:space-between}
.brand{display:flex;align-items:center;gap:10px;color:var(--white);font-weight:600;font-size:19px}
.brand-dot{width:22px;height:22px;border-radius:50%;background:var(--green)}
.nav-links{display:flex;align-items:center;gap:52px;font-size:13px;color:var(--white)}
.nav-links .active{color:var(--green)}
.hero-copy{position:absolute;left:141px;top:168px;width:480px;color:var(--white)}
.hero-copy h1{font-size:47px;line-height:57px;font-weight:600}
.hero-copy .tag{font-size:17px;font-weight:500;margin-top:6px}
.hero-copy p{font-size:12.4px;line-height:22px;margin-top:18px}
.hero-copy .btn{margin-top:30px}
.hero-wave{position:absolute;left:0;bottom:0}

/* about */
.about-photo{left:141px;top:745px;width:390px;height:390px}
.about-copy{left:580px;top:752px;width:478px}
.about-copy h2{font-size:32px;font-weight:600;color:var(--ink)}
.about-copy p{font-size:11.3px;line-height:19.3px;margin-top:14px}
.about-copy .btn{margin-top:18px}

/* services */
.services{position:absolute;left:0;top:1218px;width:1200px;height:817px;background:var(--soft)}
.section-title{text-align:center;font-size:33px;font-weight:600;color:var(--ink)}
.services .section-title{position:absolute;top:60px;width:100%}
.tabs{position:absolute;left:141px;top:122px;width:918px;height:148px;display:flex;border-bottom:1px solid #ddd}
.tab{flex:1;display:flex;flex-direction:column;align-items:center;justify-content:center;gap:10px;font-size:13px;text-align:center;line-height:16px;color:var(--ink)}
.tab.on{background:var(--ink);color:var(--white);flex:0 0 170px;border-radius:3px 3px 0 0}
.tab-icon{width:44px;height:44px;border:2px solid var(--green);border-radius:8px}
.svc-copy{position:absolute;left:141px;top:316px;width:428px}
.svc-copy h3{font-size:24px;font-weight:500;color:var(--green)}
.svc-copy p{font-size:11.3px;line-height:19.3px;margin-top:10px}
.svc-copy .btn{margin-top:18px}
.svc-photo{position:absolute;left:671px;top:311px;width:388px;height:303px;background:radial-gradient(circle at 50% 45%,#f2f2f2,#dcdcdc);border-radius:2px}
.arrow{position:absolute;top:444px;width:36px;height:36px;border-radius:50%}
.arrow.prev{left:84px;border:1.5px solid var(--ink)}
.arrow.next{left:1080px;background:var(--ink)}

/* cta */
.cta{position:absolute;left:141px;top:1907px;width:918px;height:267px;background:linear-gradient(135deg,#4e5a60,#6d7a7a 50%,#56625f);border-radius:3px;text-align:center;color:var(--white);padding-top:50px}
.cta h2{font-size:33px;font-weight:600}
.cta p{font-size:14px;line-height:24px;margin:12px auto 0;width:700px}
.cta .btn{margin-top:10px;font-size:12px;padding:9px 16px}

/* team */
.team .section-title{position:absolute;top:2250px;width:100%}
.card{position:absolute;top:2362px;width:402px;height:224px;border:1px solid #e6e6e6;border-radius:6px;background:var(--white)}
.portrait{position:absolute;top:2323px;width:120px;height:120px;background:linear-gradient(160deg,#b9b2a7,#6d655c);border-radius:3px}
.person{position:absolute;top:2396px}
.person h4{font-size:21px;font-weight:500;color:var(--green)}
.person span{font-size:14px;font-weight:500;color:var(--ink)}
.bio{position:absolute;top:2462px;width:362px;font-size:11.3px;line-height:20.5px}
.team-btn{position:absolute;left:547px;top:2615px}

/* contact */
.map{position:absolute;left:0;top:2735px;width:600px;height:423px;background:linear-gradient(135deg,#eef0f2,#e3e7ea)}
.contact{position:absolute;left:600px;top:2735px;width:600px;height:423px;background:var(--green)}
.contact h2{position:absolute;left:70px;top:52px;font-size:32px;font-weight:600;color:var(--ink)}
.field{position:absolute;left:70px;width:389px;height:42px;background:rgba(255,255,255,.15);display:flex;align-items:center;gap:10px;padding-left:14px;font-size:11.5px;color:var(--ink)}
.field svg{width:14px;height:14px}
.submit{position:absolute;left:70px;top:325px;width:389px;height:38px;background:var(--ink);color:var(--white);font-size:13px;font-weight:500;display:flex;align-items:center;justify-content:center}

/* footer */
.footer{position:absolute;left:0;top:3158px;width:1200px;height:335px;background:var(--ink);color:var(--white)}
.footer h5{position:absolute;top:62px;font-size:16px;font-weight:500}
.info{position:absolute;left:141px;display:flex;align-items:center;gap:12px;font-size:13px;line-height:19px}
.ico{width:38px;height:38px;border-radius:50%;background:#3a434b;display:flex;align-items:center;justify-content:center;flex:none}
.social{position:absolute;left:557px;display:flex;align-items:center;gap:14px;font-size:13px}
.social .ico{width:32px;height:32px}
.social .ico i{width:10px;height:10px;border-radius:50%;background:var(--white);display:block}
.foot-brand{position:absolute;left:840px;top:100px;width:230px;text-align:center;font-size:23px;font-weight:500}
.foot-brand .mark{width:110px;height:110px;border-radius:50%;background:var(--green);margin:0 auto 18px}
.copyright{position:absolute;left:0;top:3493px;width:1200px;height:41px;background:var(--green);display:flex;align-items:center;justify-content:center;font-size:14px;color:var(--ink)}
</style>
</head>
<body>

<header class="hero">
  <div class="hero-photo" role="img" aria-label="Two colleagues reviewing documents together in a bright open-plan office"></div>
  <div class="hero-shade"></div>
  <nav class="nav">
    <div class="brand"><span class="brand-dot"></span>Tollbrook Advisory</div>
    <div class="nav-links">
      <span class="active">Home</span><span>About</span><span>Services</span><span>Team</span>
      <span class="btn">Contact Us</span>
    </div>
  </nav>
  <div class="hero-copy">
    <h1>Building Success in Southern California</h1>
    <div class="tag"><span class="accent">Expertise at Every Step</span> : From Planning to Execution</div>
    <p>At Tollbrook, we blend innovative strategies with local market expertise to guide your commercial real estate ventures. Whether you're launching a new restaurant, investing in retail spaces, or expanding a franchise, our dedicated team is here to turn your real estate aspirations into tangible success. Dive into a partnership that grows with you.</p>
    <span class="btn">Contact Us</span>
  </div>
  <svg class="hero-wave" width="1200" height="140" viewBox="0 0 1200 140">
    <path d="M0 140 L0 122 L600 18 L1200 130 L1200 140 Z" fill="#fff"/>
    <path d="M0 122 L600 18 L1200 130" fill="none" stroke="#9cc9b2" stroke-width="9"/>
  </svg>
</header>

<section class="about">
  <svg class="abs about-photo" viewBox="0 0 390 390" role="img" aria-label="Modern commercial building with red brick facade and glass storefront">
    <defs><linearGradient id="bld" x1="0" y1="0" x2="1" y2="1"><stop offset="0" stop-color="#b76a55"/><stop offset=".55" stop-color="#8f8a86"/><stop offset="1" stop-color="#d9d9d9"/></linearGradient></defs>
    <rect x="57" y="57" width="276" height="276" rx="70" transform="rotate(45 195 195)" fill="url(#bld)"/>
  </svg>
  <div class="abs about-copy">
    <h2>About Tollbrook <span class="accent">Advisory</span></h2>
    <p>Welcome to Tollbrook Advisory, your trusted partner in navigating the complexities of the real estate and small business markets. Founded by industry veterans Elena Marquez and Daniel Okafor, we specialize in providing comprehensive services tailored to the unique needs of our clients. Whether you're a franchisee, a new restaurant owner, or a commercial real estate investor, our expertise in due diligence, construction management, and investment property evaluation ensures you make informed, strategic decisions.</p>
    <p>At Tollbrook Advisory, we are committed to your success. Our approach combines meticulous analysis, strategic insights, &amp; personalized service to help you achieve your business goals. We pride ourselves on our ability to deliver results that exceed expectations, fostering long-term relationships built on trust &amp; excellence.</p>
    <p style="margin-top:8px">Discover how Tollbrook Advisory can support your business journey. Partner with us and experience the difference our dedication and expertise can make.</p>
    <span class="btn">Contact Us</span>
  </div>
</section>

<section class="services">
  <h2 class="section-title">Tollbrook <span class="accent">Services</span></h2>
  <div class="tabs">
    <div class="tab on"><span class="tab-icon"></span>Franchise Development<br>&amp; Launch</div>
    <div class="tab"><span class="tab-icon"></span>Due Diligence<br>Services</div>
    <div class="tab"><span class="tab-icon"></span>Building &amp; Construction<br>Management</div>
    <div class="tab"><span class="tab-icon"></span>Investment Property<br>Evaluation</div>
    <div class="tab"><span class="tab-icon"></span>Market Analysis &amp;<br>Feasibility Studies</div>
  </div>
  <div class="svc-copy">
    <h3>Franchise Development &amp; Launch</h3>
    <p>At Tollbrook Advisory, our Franchise Development &amp; Launch service is designed to transform your successful business into a thriving franchise. We start by thoroughly evaluating your business model to determine its franchisability. Once confirmed, our team handles every aspect of the franchise setup, including legal documentation, branding, marketing strategies, operational guidelines, and franchisee recruitment.</p>
    <p>Our goal is to ensure a seamless and efficient transition from a single successful location to a robust franchise network, empowering your business to scale effectively and achieve exponential growth. Partner with us to turn your business into a nationwide brand.</p>
    <span class="btn">Contact Us</span>
  </div>
  <div class="svc-photo" role="img" aria-label="Colored push pins connected by red string forming a network"></div>
  <svg class="arrow prev" viewBox="0 0 36 36"><path d="M24 18H12M17 13l-5 5 5 5" fill="none" stroke="#222a31" stroke-width="1.8"/></svg>
  <svg class="arrow next" viewBox="0 0 36 36"><path d="M12 18h12M19 13l5 5-5 5" fill="none" stroke="#fff" stroke-width="1.8"/></svg>
</section>

<section class="cta" role="img" aria-label="Aerial view of a commercial office park with trees and parking">
  <h2>Unlock Your Business <span class="accent">Potential Today!</span></h2>
  <p>At Tollbrook Advisory, we're dedicated to turning your business aspirations into reality. Our expertise and commitment ensure you make informed, strategic decisions that drive success. Take the first step towards achieving your goals with confidence.</p>
  <span class="btn">Get Started Now</span>
</section>

<section class="team">
  <h2 class="section-title">Our Leadership <span class="accent">Team</span></h2>
  <div class="card" style="left:184px"></div>
  <div class="portrait" style="left:141px" role="img" aria-label="Portrait photo of Daniel Okafor"></div>
  <div class="person" style="left:284px"><h4>Daniel Okafor</h4><span>Principal</span></div>
  <p class="bio" style="left:202px">Daniel Okafor is a seasoned real estate expert with extensive experience in project and construction management, and a licensed real estate agent in California. Fluent in both English and Korean, he specializes in commercial real estate, bringing invaluable expertise to Tollbrook Advisory...</p>
  <div class="card" style="left:657px"></div>
  <div class="portrait" style="left:614px;background:linear-gradient(160deg,#cfdbe6,#8d9aa6)" role="img" aria-label="Portrait photo of Elena Marquez"></div>
  <div class="person" style="left:757px"><h4>Elena Marquez</h4><span>Principal</span></div>
  <p class="bio" style="left:675px">Elena Marquez brings almost 20 years of rich experience as a real estate investor and a pivotal role at one of southern California's largest real estate management firms, where she led sales and marketing strategies to elevate property value and investor returns. Her vast expertise spans...</p>
  <span class="btn team-btn">Contact Us</span>
</section>

<div class="map" role="img" aria-label="Street map of the office neighborhood with a location pin"></div>
<section class="contact">
  <h2>Contact <span style="color:#fff">Us</span></h2>
  <div class="field" style="top:106px"><svg viewBox="0 0 14 14"><circle cx="7" cy="4.5" r="3" fill="none" stroke="#222a31"/><path d="M1.5 13c0-3 2.5-5 5.5-5s5.5 2 5.5 5" fill="none" stroke="#222a31"/></svg>Your Name*</div>
  <div class="field" style="top:160px"><svg viewBox="0 0 14 14"><rect x="1" y="3" width="12" height="8.5" fill="none" stroke="#222a31"/><path d="M1 3l6 5 6-5" fill="none" stroke="#222a31"/></svg>Your Email*</div>
  <div class="field" style="top:214px"><svg viewBox="0 0 14 14"><path d="M3 1.5l2.5 3-1.5 1.5c1 2 2 3 4 4l1.5-1.5 3 2.5-1.5 2c-5 0-9.5-4.5-9.5-9.5z" fill="none" stroke="#222a31"/></svg>Your Phone*</div>
  <div class="field" style="top:268px"><svg viewBox="0 0 14 14"><circle cx="7" cy="3" r="1.5" fill="#222a31"/><path d="M7 6v7" stroke="#222a31" stroke-width="1.5"/></svg>Additional Information</div>
  <div class="submit">Submit Now</div>
</section>

<footer class="footer">
  <h5 style="left:141px">Contact Details</h5>
  <div class="info" style="top:108px"><span class="ico"><svg width="14" height="16" viewBox="0 0 14 16"><path d="M7 15s5-5 5-9A5 5 0 0 0 2 6c0 4 5 9 5 9z" fill="#9cc9b2"/><circle cx="7" cy="6" r="1.8" fill="#3a434b"/></svg></span><span>214 Harbor View Rd Suite 300<br>Costa Verde, CA 90000, USA</span></div>
  <div class="info" style="top:175px"><span class="ico"><svg width="14" height="14" viewBox="0 0 14 14"><path d="M3 1.5l2.5 3-1.5 1.5c1 2 2 3 4 4l1.5-1.5 3 2.5-1.5 2c-5 0-9.5-4.5-9.5-9.5z" fill="#9cc9b2"/></svg></span><span>Phone<br>555 010 2046</span></div>
  <div class="info" style="top:243px"><span class="ico"><svg width="14" height="12" viewBox="0 0 14 12"><rect x="1" y="1" width="12" height="10" fill="#9cc9b2"/><path d="M1 1l6 5 6-5" fill="none" stroke="#3a434b"/></svg></span><span>Email<br>info@tollbrookadvisory.example</span></div>
  <h5 style="left:557px">Follow Us</h5>
  <div class="social" style="top:116px"><span class="ico"><i></i></span>Friendlane</div>
  <div class="social" style="top:163px"><span class="ico"><i></i></span>Snapgrid</div>
  <div class="social" style="top:210px"><span class="ico"><i></i></span>Chirpline</div>
  <div class="social" style="top:257px"><span class="ico"><i></i></span>Streamtube</div>
  <div class="foot-brand"><div class="mark"></div>Tollbrook Advisory</div>
</footer>
<div class="copyright">©2024 Tollbrook Advisory. All Rights Reserved.</div>

</body>
</html>
```